business card

Business card for new business.
Red and black corporate colors.
Card can have an Indsutrial feel to it. Feel free to add Rust, Bolted steel, or graphics as you see fit. We provide highly specialized services to the below mentioned industries.
Keep information out of corners so that if I want I can choose rounded corners.
Information
- front. name - title - phone - email
- Rear
Pipelines - Marine - Utilities - Forestry - Power
Northgate - Red Ridge - Harlow Bay - Stonefield - Westmere

```html
<!DOCTYPE html>
<html lang="en">
<head>
<meta charset="utf-8">
<title>Girderline business card</title>
<link rel="stylesheet" href="https://fonts.googleapis.com/css2?family=Open+Sans:wght@400;600;800&display=swap">
<style>
  :root {
    --stage: #3a3b3d;
    --card-dark: #1f2123;
    --card-dark-edge: #2b2d30;
    --card-light: #f7f7f7;
    --brand-red: #e3141b;
    --steel-grey: #8a8c8f;
    --text-grey: #6d6f72;
    --text-light: #f2f2f2;
  }
  * { box-sizing: border-box; margin: 0; padding: 0; }
  html, body { width: 1200px; height: 900px; overflow: hidden; }
  body {
    background: var(--stage);
    font-family: "Open Sans", Arial, sans-serif;
    position: relative;
  }
  .card {
    position: absolute;
    left: 220px;
    width: 760px;
    height: 420px;
    overflow: hidden;
    box-shadow: 0 12px 30px rgba(0,0,0,.45);
  }
  /* Rear side */
  .card--rear {
    top: 25px;
    background: linear-gradient(135deg, var(--card-dark-edge), var(--card-dark) 60%);
    color: var(--text-light);
    text-align: center;
  }
  .wordmark {
    display: inline-flex;
    align-items: center;
    gap: 14px;
    font-weight: 800;
    letter-spacing: 1px;
    line-height: 1;
    white-space: nowrap;
  }
  .wordmark__square {
    width: .6em; height: .6em;
    background: var(--brand-red);
  }
  .card--rear .wordmark {
    margin-top: 110px;
    font-size: 64px;
    color: var(--steel-grey);
  }
  .industries {
    margin-top: 46px;
    font-size: 19px;
    line-height: 1.45;
    font-weight: 400;
  }
  .industries .dot { color: var(--brand-red); padding: 0 4px; }

  /* Front side */
  .card--front {
    top: 465px;
    background: var(--card-light);
  }
  .flag-pole {
    position: absolute;
    left: 0; top: 0;
  }
  .person {
    position: absolute;
    left: 470px; top: 82px;
  }
  .person__name {
    color: var(--brand-red);
    font-weight: 800;
    font-size: 28px;
    line-height: 1;
    white-space: nowrap;
  }
  .person__title {
    color: var(--text-grey);
    font-size: 15px;
    font-weight: 600;
    letter-spacing: .5px;
    margin-top: 4px;
  }
  .contact {
    position: absolute;
    left: 470px; top: 230px;
    list-style: none;
    color: var(--text-grey);
    font-size: 16px;
  }
  .contact li {
    display: flex; align-items: center; gap: 10px;
    line-height: 24px;
    white-space: nowrap;
  }
  .contact svg { width: 16px; height: 16px; fill: var(--brand-red); }
  .card--front .wordmark {
    position: absolute;
    left: 70px; top: 300px;
    font-size: 46px;
    color: var(--steel-grey);
  }
</style>
</head>
<body>

<section class="card card--rear" aria-label="Card rear">
  <div class="wordmark"><span class="wordmark__square"></span>GIRDERLINE</div>
  <p class="industries">
    Pipelines <span class="dot">•</span>Marine <span class="dot">•</span>Utilities <span class="dot">•</span>Forestry<br>
    Power <span class="dot">•</span>Northgate <span class="dot">•</span>Red Ridge <span class="dot">•</span>Harlow Bay<br>
    Stonefield <span class="dot">•</span>Westmere
  </p>
</section>

<section class="card card--front" aria-label="Card front">
  <svg class="flag-pole" width="760" height="420" viewBox="0 0 760 420" aria-hidden="true">
    <line x1="448" y1="90" x2="448" y2="270" stroke="var(--brand-red)" stroke-width="3"/>
    <polygon points="448,84 448,108 428,96" fill="var(--brand-red)"/>
  </svg>

  <div class="person">
    <p class="person__name">MARK HALDEN</p>
    <p class="person__title">PRESIDENT</p>
  </div>

  <ul class="contact">
    <li>
      <svg viewBox="0 0 16 16" aria-hidden="true"><path d="M3.6 1.5l2.2 2.6-1.3 1.7c.9 2 2.5 3.6 4.5 4.5l1.7-1.3 2.6 2.2-1.2 2.3C7 13.3 2.7 9 2.3 3.1z"/></svg>
      555 0142 7788
    </li>
    <li>
      <svg viewBox="0 0 16 16" aria-hidden="true"><path d="M1 3.5h14v1.2L8 9 1 4.7zM1 6.4l7 4.3 7-4.3v6.1H1z"/></svg>
      mark@girderline.com
    </li>
    <li>
      <svg viewBox="0 0 16 16" aria-hidden="true"><circle cx="8" cy="8" r="6.5"/><path d="M1.5 8h13M8 1.5c2.2 2 2.2 11 0 13M8 1.5c-2.2 2-2.2 11 0 13" stroke="#fff" stroke-width="1" fill="none"/></svg>
      www.girderline.com
    </li>
  </ul>

  <div class="wordmark"><span class="wordmark__square"></span>GIRDERLINE</div>
</section>

</body>
</html>
```